Web Design

We need a website for a company based in Doha Qatar called
Lumara Maid Service.

It is the number one maid cleaning service company, and we have branches all over qatar.

Luxury Cleaning Service Provider.

The color scheme is gold, yellow and black like the logo.

Before they get to the website, there is an intro video.

The website should depict luxury.

Target Market(s)

People who need maids at their houses.

Industry/Entity Type

Cleaning Service

Requirements
Must have
• Luxury, Sleek, Modern

The opening sequence is a video which I already have. Its too big to upload here so I am going to put it on youtube.

After the opening sequence, the home page should have a widescreen photo background and it should change every five seconds, the first background photo should be of qatar westbay skyline. Then the second background should be of maid photos in cleaning positions. Then the third background should be of cleaner photos etc.

We will send you all the tabs and all the content later.

```html
<!DOCTYPE html>
<html lang="en">
<head>
<meta charset="UTF-8">
<title>Lumara Maid Service</title>
<link rel="stylesheet" href="https://fonts.googleapis.com/css2?family=Bebas+Neue&family=Open+Sans:wght@400;600&family=Oxygen:wght@400&display=swap">
<style>
  :root {
    --yellow: #fff67a;
    --gold: #c8902a;
    --black: #000000;
    --white: #ffffff;
    --ink: #1a1a1a;
    --body-font: "Open Sans", Arial, sans-serif;
    --display-font: "Bebas Neue", Impact, sans-serif;
    --footer-font: "Oxygen", Arial, sans-serif;
  }
  * { box-sizing: border-box; margin: 0; padding: 0; }
  html, body { width: 1200px; height: 800px; overflow: hidden; background: var(--white); }
  body { position: relative; font-family: var(--body-font); }

  .site-header { position: absolute; top: 0; left: 0; width: 1200px; height: 100px; background: var(--white); }
  .brand { position: absolute; left: 100px; top: 36px; display: flex; align-items: center; gap: 10px; }
  .brand-dot { width: 22px; height: 22px; border-radius: 50%; background: var(--gold); }
  .brand-name { font-family: var(--body-font); font-weight: 600; font-size: 18px; color: var(--gold); }

  .main-nav { position: absolute; top: 33px; left: 524px; display: flex; height: 42px; }
  .main-nav a { display: block; height: 42px; line-height: 42px; font-size: 14px; color: var(--ink); text-decoration: none; padding: 0 20px; }
  .main-nav a + a { margin-left: 15px; }
  .main-nav a.is-active { background: var(--yellow); border-radius: 4px; }

  .hero { position: absolute; top: 100px; left: 0; width: 1200px; height: 600px; overflow: hidden; }
  .hero-photo { position: absolute; top: 0; height: 600px; }
  .photo-window { left: 0; width: 310px; background: linear-gradient(160deg, #b7b1a6 0%, #8e7c6b 45%, #5a4a3f 100%); }
  .photo-table { left: 310px; width: 527px; background: linear-gradient(170deg, #d8d9d6 0%, #a8a49a 45%, #6f5a48 80%, #4a3a2e 100%); }
  .photo-corridor { left: 837px; width: 363px; background: linear-gradient(180deg, #e4e4e2 0%, #cfd0ce 50%, #2f4a8a 80%, #273f7a 100%); }
  .hero-shade { position: absolute; inset: 0; background: rgba(0,0,0,0.12); }

  .hero-copy { position: absolute; left: 100px; top: 188px; width: 530px; }
  .hero-title { font-family: var(--display-font); font-weight: 400; font-size: 48px; line-height: 52px; color: var(--yellow); letter-spacing: 0.5px; }
  .hero-text { margin-top: 16px; font-size: 17px; line-height: 30px; color: var(--white); }
  .hero-button { display: inline-block; margin-top: 22px; width: 134px; height: 54px; line-height: 56px; text-align: center; background: var(--yellow); color: var(--black); font-family: var(--display-font); font-size: 24px; text-decoration: none; }

  .slider-arrow { position: absolute; top: 288px; }
  .slider-arrow.prev { left: 44px; }
  .slider-arrow.next { left: 1132px; }

  .slider-dots { position: absolute; top: 575px; left: 1026px; display: flex; gap: 8px; }
  .slider-dots span { width: 13px; height: 13px; border-radius: 50%; background: var(--white); }
  .slider-dots span.is-active { background: var(--yellow); }

  .site-footer { position: absolute; top: 700px; left: 0; width: 1200px; height: 100px; background: var(--black); color: var(--white); font-family: var(--footer-font); }
  .footer-nav { position: absolute; left: 98px; top: 24px; font-size: 17px; }
  .footer-nav a { color: var(--white); text-decoration: none; }
  .footer-nav .sep { margin: 0 8px; }
  .copyright { position: absolute; left: 98px; top: 58px; font-size: 13px; }
  .social { position: absolute; left: 978px; top: 38px; display: flex; gap: 10px; }
  .social span { width: 23px; height: 23px; border-radius: 2px; }
  .social .s1 { background: #3b5998; }
  .social .s2 { background: #4fb5e6; }
  .social .s3 { background: #0e76a8; }
  .social .s4 { background: #f08a1c; }
</style>
</head>
<body>
  <header class="site-header">
    <div class="brand">
      <span class="brand-dot"></span>
      <span class="brand-name">Lumara Maid Service</span>
    </div>
    <nav class="main-nav">
      <a href="#" class="is-active">Home</a>
      <a href="#">About Us</a>
      <a href="#">Services</a>
      <a href="#">Testimonals</a>
      <a href="#">Contact Us</a>
    </nav>
  </header>

  <section class="hero">
    <div class="hero-photo photo-window" role="img" aria-label="Maid cleaning a window with a steam cleaner"></div>
    <div class="hero-photo photo-table" role="img" aria-label="Housekeeper wiping an office desk"></div>
    <div class="hero-photo photo-corridor" role="img" aria-label="Cleaner vacuuming a blue carpeted corridor"></div>
    <div class="hero-shade"></div>

    <div class="hero-copy">
      <h1 class="hero-title">Lorem Ipsum Dolor Sit Amet</h1>
      <p class="hero-text">Nulla consequat massa quis enim. Donec pede justo, fringilla vel, aliquet nec, vulputate eget, arcu. In enim justo, rhoncus ut, imperdiet a, venenatis vitae, justo.</p>
      <a href="#" class="hero-button">Read More +</a>
    </div>

    <svg class="slider-arrow prev" width="24" height="38" viewBox="0 0 24 38" aria-label="Previous slide">
      <polyline points="19,3 5,19 19,35" fill="none" stroke="#ffffff" stroke-width="7" stroke-linejoin="round"/>
    </svg>
    <svg class="slider-arrow next" width="24" height="38" viewBox="0 0 24 38" aria-label="Next slide">
      <polyline points="5,3 19,19 5,35" fill="none" stroke="#ffffff" stroke-width="7" stroke-linejoin="round"/>
    </svg>

    <div class="slider-dots">
      <span></span><span></span><span class="is-active"></span>
    </div>
  </section>

  <footer class="site-footer">
    <nav class="footer-nav">
      <a href="#">Home</a><span class="sep">|</span><a href="#">About Us</a><span class="sep">|</span><a href="#">Services</a><span class="sep">|</span><a href="#">Products</a><span class="sep">|</span><a href="#">Contact Us</a><span class="sep">|</span><a href="#">Blog</a>
    </nav>
    <p class="copyright">© 2014 Company Name&nbsp; All right reserved&nbsp; Term of Use</p>
    <div class="social">
      <span class="s1"></span><span class="s2"></span><span class="s3"></span><span class="s4"></span>
    </div>
  </footer>
</body>
</html>
```